Landing Page Design for Adult Dating Age Verification (18+)

The objective of this task is to design a visually appealing pre-landing page for the adult dating site "Quillmera (site: https://quillmera.com/)" with an age verification mechanism. The pre-landing page will feature two buttons that redirect visitors to the main offer. The design should also include a footer block that includes links to the terms of use, privacy policy, and contact us pages.

Design Requirements:
Develop an age verification section prominently displayed on the pre-landing page.
Design the section to include two buttons labeled "Yes" and "No" for visitors to confirm their age.
Ensure the section is visually appealing and clearly communicates the purpose of age verification.

Visual Appeal:
Create a visually appealing design that aligns with the branding and theme of the "Quillmera" adult dating site.
Use suitable color schemes, typography, and graphics to enhance the overall visual appeal of the pre-landing page.

Layout and Navigation:
Design an engaging and intuitive layout that encourages visitors to interact with the page and proceed to the main offer.
Ensure clear and visible navigation elements that direct visitors to the main offer or provide additional information.

Responsive Design:
Develop a responsive design that provides a seamless user experience across various devices, including desktop and mobile.
Ensure the design elements and layout adapt well to different screen sizes and resolutions.

File Formats and Assets:
Deliver the final design in PSD, AI, or Sketch format, ensuring that the files are well-organized and layered.
Include any necessary images or assets used in the design, ensuring they are of high quality and optimized for web use.

```html
<!DOCTYPE html>
<html lang="en">
<head>
<meta charset="utf-8">
<title>Quillmera – Age Verification</title>
<link rel="stylesheet" href="https://fonts.googleapis.com/css2?family=Cinzel:wght@600;700&family=Roboto:wght@400;500;700&display=swap">
<style>
  :root {
    --lavender: #d6a5dc;
    --navy: #272838;
    --white: #ffffff;
    --panel: rgba(40, 28, 30, 0.72);
    --hero-a: #3a3346;
    --hero-b: #5b4a55;
    --hero-c: #2c2d3d;
  }
  * { box-sizing: border-box; margin: 0; padding: 0; }
  html, body { width: 1200px; height: 834px; overflow: hidden; }
  body { font-family: "Roboto", sans-serif; background: var(--navy); color: var(--white); position: relative; }

  .site-header { position: absolute; left: 0; top: 0; width: 1200px; height: 114px; background: var(--white); }
  .header-band { position: absolute; left: 0; top: 114px; width: 1200px; height: 7px; background: var(--lavender); }

  .brand { position: absolute; display: flex; align-items: center; gap: 10px; text-decoration: none; }
  .brand-dot { width: 30px; height: 30px; border-radius: 50%; background: var(--lavender); }
  .brand-name { font-family: "Cinzel", serif; font-weight: 700; font-size: 26px; color: var(--navy); letter-spacing: 0.5px; }
  .site-header .brand { left: 111px; top: 42px; }
  .site-footer .brand { left: 111px; top: 762px; }
  .site-footer .brand-name { color: var(--white); }

  .btn { position: absolute; display: flex; align-items: center; justify-content: center; border-radius: 24px; font-family: "Roboto", sans-serif; font-weight: 500; text-decoration: none; text-transform: uppercase; }
  .btn-fill { background: var(--lavender); color: var(--white); }
  .btn-outline { background: var(--white); color: var(--navy); border: 2px solid var(--lavender); }
  .btn-signin { left: 848px; top: 37px; width: 114px; height: 46px; font-size: 16px; box-shadow: 0 4px 12px rgba(214,165,220,0.45); }
  .btn-join { left: 975px; top: 37px; width: 113px; height: 46px; font-size: 16px; box-shadow: 0 4px 12px rgba(214,165,220,0.35); }

  .hero-photo { position: absolute; left: 0; top: 121px; width: 1200px; height: 598px;
    background: radial-gradient(ellipse at 55% 45%, var(--hero-b) 0%, var(--hero-a) 45%, var(--hero-c) 100%); }

  .age-gate { position: absolute; left: 347px; top: 273px; width: 507px; height: 296px; background: var(--panel); border-radius: 8px; text-align: center; }
  .age-gate h1 { position: absolute; left: 0; top: 44px; width: 100%; font-family: "Cinzel", serif; font-weight: 700; font-size: 43px; line-height: 47px; color: var(--white); }
  .btn-yes { left: 151px; top: 165px; width: 97px; height: 42px; font-size: 17px; font-weight: 700; }
  .btn-no { left: 258px; top: 165px; width: 97px; height: 42px; font-size: 17px; font-weight: 700; }
  .remember { position: absolute; left: 0; top: 229px; width: 100%; display: flex; justify-content: center; align-items: center; gap: 8px; font-size: 14px; font-weight: 500; }
  .remember .box { width: 10px; height: 10px; border: 1.5px solid var(--white); border-radius: 2px; }

  .site-footer { position: absolute; left: 0; top: 719px; width: 1200px; height: 115px; background: var(--navy); }
  .copyright { position: absolute; left: 400px; top: 50px; width: 400px; text-align: center; font-size: 14px; }
  .copyright strong { font-weight: 500; }
  .footer-links { position: absolute; right: 111px; top: 51px; font-size: 12.5px; display: flex; gap: 10px; }
  .footer-links a { color: var(--white); text-decoration: none; }
  .site-code { position: absolute; left: 1142px; top: 54px; font-size: 10px; }
</style>
</head>
<body>
  <header class="site-header">
    <a class="brand" href="https://quillmera.com/"><span class="brand-dot"></span><span class="brand-name">Quillmera</span></a>
    <a class="btn btn-fill btn-signin" href="#">Sign In</a>
    <a class="btn btn-outline btn-join" href="#">Join Now</a>
  </header>
  <div class="header-band"></div>

  <div class="hero-photo" role="img" aria-label="Photograph of an intimate couple embracing on a bed with dark sheets"></div>

  <section class="age-gate">
    <h1>ARE YOU OVER 18<br>YEARS OF AGE?</h1>
    <a class="btn btn-fill btn-yes" href="#">Yes</a>
    <a class="btn btn-outline btn-no" href="#">No</a>
    <label class="remember"><span class="box"></span>Remember me</label>
  </section>

  <footer class="site-footer">
    <a class="brand" href="https://quillmera.com/"><span class="brand-dot"></span><span class="brand-name">Quillmera</span></a>
    <p class="copyright">© 2023 <strong>Quillmera</strong> &nbsp;|&nbsp; All Rights Reserved</p>
    <nav class="footer-links"><a href="#">Privacy Policy</a><span>|</span><a href="#">Terms Of Use</a><span>|</span><a href="#">Contact Us</a></nav>
    <span class="site-code">C45</span>
  </footer>
</body>
</html>
```